BRISKEL Need a luxury modern business card designed.

Need a luxury modern business card designed. refer to the uploaded files for the company name and logo in the zip file under source files. i will making my descion on monday. so please send in before then so if we need to edit we will have the time. we have a trade show coming up and im on a deadline for printer.

Target Market(s)

high end clients

Contact Information for Business Card

Company nAme and logo. Tobias Fennick Co-Founder / Project Manager Office # 555-318-7094 Cell # 555-642-1586 BRISKEL.CA Tobias@briskel-example.ca

Font styles to use
Other font styles liked:
• Modern

Requirements
Must have
• Company name and logo, contact info, using the black, gold and white color scheme.

```html
<!DOCTYPE html>
<html lang="en">
<head>
<meta charset="utf-8">
<title>BRISKEL Business Card</title>
<link href="https://fonts.googleapis.com/css2?family=Josefin+Sans:wght@300&family=Raleway:wght@700&family=Open+Sans:wght@400&display=swap" rel="stylesheet">
<style>
  :root {
    --backdrop: #d9d9d9;
    --card: #333333;
    --gold: #a69865;
    --white: #ffffff;
    --text: #f2f2f2;
  }
  * { margin: 0; padding: 0; box-sizing: border-box; }
  html, body {
    width: 1200px;
    height: 802px;
    overflow: hidden;
    background: var(--backdrop);
  }
  .canvas {
    position: relative;
    width: 1200px;
    height: 802px;
  }
  .card {
    position: absolute;
    top: 274px;
    width: 444px;
    height: 265px;
    background: var(--card);
    box-shadow: 0 3px 6px rgba(0, 0, 0, 0.35);
    overflow: hidden;
  }
  .card--front { left: 136px; }
  .card--back { left: 624px; }

  .wordmark {
    font-family: "Josefin Sans", sans-serif;
    font-weight: 300;
    color: var(--white);
    letter-spacing: 0.2em;
    line-height: 1;
    white-space: nowrap;
  }
  .card--front .wordmark {
    position: absolute;
    left: 23px;
    top: 42px;
    font-size: 34px;
  }
  .card--back .wordmark {
    position: absolute;
    left: 0;
    right: 0;
    top: 158px;
    text-align: center;
    font-size: 38px;
    padding-left: 0.2em;
  }

  .brand-block {
    position: absolute;
    right: 0;
    top: 40px;
    width: 185px;
    height: 185px;
    background: var(--gold);
  }
  .brand-mark {
    position: absolute;
    left: 204px;
    top: 78px;
    width: 36px;
    height: 36px;
    background: var(--gold);
  }

  .holder {
    position: absolute;
    left: 23px;
    top: 124px;
  }
  .holder__name {
    font-family: "Raleway", sans-serif;
    font-weight: 700;
    font-size: 16px;
    color: var(--gold);
    text-transform: uppercase;
    line-height: 1.2;
  }
  .holder__role {
    font-family: "Open Sans", sans-serif;
    font-size: 11.5px;
    color: var(--text);
    line-height: 16px;
  }

  .contact {
    position: absolute;
    left: 23px;
    top: 190px;
    list-style: none;
    font-family: "Open Sans", sans-serif;
    font-size: 11.5px;
    color: var(--text);
  }
  .contact__item {
    display: flex;
    align-items: center;
    gap: 6px;
    height: 16px;
  }
  .contact__icon {
    width: 10px;
    height: 10px;
    fill: var(--gold);
    flex: none;
  }
</style>
</head>
<body>
<main class="canvas">
  <section class="card card--front" aria-label="Business card front">
    <div class="wordmark">BRISKEL</div>

    <div class="brand-block" role="img" aria-label="Brand decoration area"></div>

    <div class="holder">
      <p class="holder__name">Tobias Fennick</p>
      <p class="holder__role">Co-Founder</p>
      <p class="holder__role">Project Manager</p>
    </div>

    <ul class="contact">
      <li class="contact__item">
        <svg class="contact__icon" viewBox="0 0 10 10" aria-hidden="true">
          <path d="M0 3.5 Q5 0 10 3.5 L10 4.5 L7.5 4.5 L7 3.5 L3 3.5 L2.5 4.5 L0 4.5 Z M2 5 L8 5 L9 9 L1 9 Z"/>
        </svg>
        <span>555-318-7094</span>
      </li>
      <li class="contact__item">
        <svg class="contact__icon" viewBox="0 0 10 10" aria-hidden="true">
          <path d="M2.5 0 H7.5 V10 H2.5 Z M3.5 1.2 V7.8 H6.5 V1.2 Z" fill-rule="evenodd"/>
        </svg>
        <span>555-642-1586</span>
      </li>
      <li class="contact__item">
        <svg class="contact__icon" viewBox="0 0 10 10" aria-hidden="true">
          <path d="M0 2 H10 V8 H0 Z M0.8 2.6 L5 5.6 L9.2 2.6 Z" fill-rule="evenodd"/>
        </svg>
        <span>briskel.ca tobias@briskel-example.ca</span>
      </li>
    </ul>
  </section>

  <section class="card card--back" aria-label="Business card back">
    <div class="brand-mark" aria-hidden="true"></div>
    <div class="wordmark">BRISKEL</div>
  </section>
</main>
</body>
</html>
```